BFCM Creatives Theme

We are looking for an initial design for our BFCM campaign this year to set the theme for all other creatives for BFCM. We are an ecommerce brand selling Merino wool baby clothing. Our flagship product is the Marlow Toddler Hush Pod (see images).

We are starting with the request for an instagram post, announcing the sale (details below). This post should be 1080x1350 but also look appealing in the square grid. I've attached a basic brand card showing color palette, fonts, and logos. I will also attach some image options. We are looking for your creativity to shine while aligning with our branding and connecting with the customer. If you have a specific idea and are looking for a specific image please contact us.

Sale Details:
- 20% Off Sitewide
- 11.28.24 - 12.02.24
- Excluding giftcards and imperfects. No rainchecks.

```html
<!DOCTYPE html>
<html lang="en">
<head>
<meta charset="utf-8">
<title>Lanora BFCM Sale Post</title>
<link href="https://fonts.googleapis.com/css2?family=Poppins:wght@500;600;700&family=Kalam:wght@300&display=swap" rel="stylesheet">
<style>
  :root {
    --stage: #3a3a3a;
    --sand: #dedbd5;
    --charcoal: #343538;
    --cream: #f1efeb;
    --white: #ffffff;
    --ink: #333333;
    --photo-light: #eeeeec;
    --photo-mid: #dfe3da;
  }
  html, body {
    margin: 0;
    width: 1200px;
    height: 1197px;
    overflow: hidden;
    background: var(--stage);
  }
  .post {
    position: absolute;
    left: 132px;
    top: 13px;
    width: 1080px;
    height: 1350px;
    transform: scale(0.8667);
    transform-origin: 0 0;
    background: var(--sand);
    overflow: hidden;
    font-family: "Poppins", sans-serif;
  }
  .post-shapes { position: absolute; inset: 0; }
  .brand-tag {
    position: absolute;
    left: 0; top: 65px;
    width: 457px; height: 105px;
    background: var(--white);
    display: flex; align-items: center; gap: 18px;
    padding-left: 34px; box-sizing: border-box;
  }
  .brand-dot {
    width: 58px; height: 58px; border-radius: 50%;
    border: 4px solid var(--ink); box-sizing: border-box;
  }
  .brand-name {
    font-weight: 500; font-size: 72px; color: var(--ink);
    letter-spacing: -1px; line-height: 1;
  }
  .offer {
    position: absolute; inset: 0; margin: 0;
    color: var(--cream); font-weight: 700; line-height: 1;
    font-size: 16px; pointer-events: none;
  }
  .offer span { position: absolute; left: 56px; white-space: nowrap; }
  .offer-amount { top: 845px; font-size: 216px; letter-spacing: -4px; }
  .offer-off { top: 1045px; font-size: 190px; letter-spacing: -2px; }
  .offer-scope { top: 1234px; font-size: 94px; letter-spacing: -1px; }
  .calendar-icon { position: absolute; left: 845px; top: 876px; width: 70px; height: 70px; }
  .sale-dates {
    position: absolute; left: 658px; top: 959px;
    width: 422px; height: 55px;
    background: var(--charcoal); color: var(--cream);
    border-radius: 28px 0 0 28px;
    font-weight: 600; font-size: 37px;
    display: flex; align-items: center; justify-content: center;
  }
  .terms {
    position: absolute; left: 712px; top: 1070px; margin: 0; padding: 0;
    list-style: none;
    font-family: "Kalam", cursive; font-weight: 300;
    font-size: 39px; line-height: 54px; color: var(--ink);
  }
  .terms li { position: relative; padding-left: 44px; }
  .terms li::before {
    content: ""; position: absolute; left: 4px; top: 24px;
    width: 13px; height: 13px; border-radius: 50%; background: var(--ink);
  }
</style>
</head>
<body>
  <main class="post">
    <svg class="post-shapes" width="1080" height="1350" viewBox="0 0 1080 1350">
      <defs>
        <linearGradient id="photoTone" x1="0" y1="0" x2="0" y2="1">
          <stop offset="0" stop-color="var(--photo-light)"/>
          <stop offset="1" stop-color="var(--photo-mid)"/>
        </linearGradient>
      </defs>
      <circle class="photo-backdrop" cx="640" cy="330" r="490" fill="var(--charcoal)"/>
      <circle class="product-photo" cx="620" cy="290" r="480" fill="url(#photoTone)"
              role="img" aria-label="Photo of a baby lying on a white sheet wearing the striped Marlow Toddler Hush Pod"/>
      <circle class="offer-rim" cx="305" cy="1160" r="388" fill="var(--cream)"/>
      <circle class="offer-disc" cx="280" cy="1160" r="383" fill="var(--charcoal)"/>
    </svg>

    <div class="brand-tag">
      <span class="brand-dot"></span>
      <span class="brand-name">lanora</span>
    </div>

    <h1 class="offer">
      <span class="offer-amount">20%</span>
      <span class="offer-off">OFF</span>
      <span class="offer-scope">Sitewide</span>
    </h1>

    <svg class="calendar-icon" viewBox="0 0 70 70" aria-hidden="true">
      <rect x="4" y="10" width="62" height="56" rx="8" fill="none" stroke="var(--charcoal)" stroke-width="5"/>
      <rect x="4" y="10" width="62" height="14" rx="6" fill="var(--charcoal)"/>
      <rect x="16" y="2" width="6" height="16" rx="3" fill="var(--charcoal)"/>
      <rect x="48" y="2" width="6" height="16" rx="3" fill="var(--charcoal)"/>
      <g fill="var(--charcoal)">
        <rect x="13" y="31" width="9" height="7"/><rect x="25" y="31" width="9" height="7"/><rect x="37" y="31" width="9" height="7"/><rect x="49" y="31" width="9" height="7"/>
        <rect x="13" y="41" width="9" height="7"/><rect x="25" y="41" width="9" height="7"/><rect x="37" y="41" width="9" height="7"/><rect x="49" y="41" width="9" height="7"/>
        <rect x="13" y="51" width="9" height="7"/><rect x="25" y="51" width="9" height="7"/><rect x="37" y="51" width="9" height="7"/>
      </g>
    </svg>

    <div class="sale-dates">11.28.24 - 12.02.24</div>

    <ul class="terms">
      <li>Excluding giftcards<br>and imperfects</li>
      <li>No rainchecks</li>
    </ul>
  </main>
</body>
</html>
```